BRANDEMEIER & BRANDEMEIER,LLP NEEDS A NEW LETTERHEAD DESIGN

a conservative yet contemporary layout befitting a long established
firm, consistent with the times, some form of logo so it catches ones attention, and is
admirable, but portrays integrity
Updates

I would like to approve #22066987 Please advise how to do this as it’s confusing on the site so I can approve payment for the designer

Target Market(s)

real estate investors and building management people

Industry/Entity Type

Law Firm

Font styles to use
Serif

Colors

Designer to choose colors to be used in the design.

Requirements
Must have
• some form of conservative logo

```html
<!DOCTYPE html>
<html lang="en">
<head>
<meta charset="utf-8">
<title>Brandemeier &amp; Brandemeier, LLP — Letterhead</title>
<link href="https://fonts.googleapis.com/css2?family=Cormorant+SC:wght@500&family=Arimo:wght@400;700&display=swap" rel="stylesheet">
<style>
  :root {
    --backdrop: #ececec;
    --paper: #f7f7f7;
    --band-dark: #27343d;
    --band-light: #3d4d58;
    --band-text: #eef1f3;
    --band-subtext: #c3ccd2;
    --ink: #2b2b2b;
  }
  * { margin: 0; padding: 0; box-sizing: border-box; }
  html, body {
    width: 1200px;
    height: 795px;
    overflow: hidden;
    background: var(--backdrop);
  }
  .letterhead {
    position: absolute;
    left: 314px;
    top: 28px;
    width: 572px;
    height: 740px;
    background: var(--paper);
    box-shadow: 0 2px 10px rgba(0,0,0,0.12);
  }
  .masthead {
    height: 70px;
    background: linear-gradient(90deg, var(--band-dark), var(--band-light));
    padding: 22px 0 0 78px;
  }
  .firm-name {
    font-family: "Cormorant SC", Georgia, serif;
    font-weight: 500;
    font-size: 20px;
    letter-spacing: 1.5px;
    color: var(--band-text);
    line-height: 1;
  }
  .practice-area {
    font-family: "Cormorant SC", Georgia, serif;
    font-size: 8.5px;
    letter-spacing: 2.2px;
    color: var(--band-subtext);
    margin-top: 3px;
  }
  .footer {
    position: absolute;
    left: 0;
    right: 0;
    bottom: 0;
  }
  .contact {
    padding: 0 0 14px 26px;
    font-family: Arimo, Arial, sans-serif;
    font-size: 10px;
    line-height: 1.3;
    color: var(--ink);
  }
  .contact .contact-firm { font-size: 11px; }
  .contact strong { font-weight: 700; }
  .contact .divider { margin: 0 4px; }
  .website {
    position: absolute;
    right: 26px;
    bottom: 60px;
    font-family: Arimo, Arial, sans-serif;
    font-size: 8px;
    letter-spacing: 2.5px;
    color: var(--ink);
  }
  .base-rule {
    height: 7px;
    background: var(--band-dark);
  }
</style>
</head>
<body>
  <main class="letterhead">
    <header class="masthead">
      <h1 class="firm-name">Brandemeier &amp; Brandemeier,LLP</h1>
      <p class="practice-area">New York City Landlord / Tenant Real Estate Law</p>
    </header>

    <footer class="footer">
      <p class="website">www.brandemeierlaw.com</p>
      <address class="contact">
        <div class="contact-firm">Brandemeier &amp; Brandemeier, LLP</div>
        <div>41 Halden Street Suite 210, Brooklyn, New York 11201</div>
        <div><strong>Phone:</strong> (718) 555-0143<span class="divider">|</span><strong>Fax:</strong> (718) 555-0178<span class="divider">|</span><strong>Email:</strong> info@bbrelaw.com</div>
      </address>
      <div class="base-rule"></div>
    </footer>
  </main>
</body>
</html>
```